New B2C website design to help dads be better dads

DadHarbor is a website to help dads be the “best dad you can be.”

We require our website to be designed into a PSD format, no coding necessary.

The general concept is a two-page design. The first page is the login page, the second page is the home page. Once at the home page, rather than navigating to and from different pages, the user will push and pull through different visual and functional layers of the hierarchy. In theory, this should add to the user experience by having a visual anchor of where they are (through layered pagination) as well as improving loading times since the new information should only be a delta in data load versus a brand new page load.

The general look-and-feel we are going for is clean, simple, minimal. This means that the winning design will show us a good eye for web-optimized typography, good use of white (negative) space, and good use of a visually pleasing grid.

We require a total of 6 page "views" plus the landing page. We note that many of the views are similar to one another.
Landing page
Milestone view
Task view
Content view, articles
Content view, products
Search view
What's new view

Please review all of the additional information provided as well as the attachments for examples.

We provide the following websites as good references for:

Typography:
http://example-kelvorn.com/journal/

Use of white space:
http://www.trenvaskit.com/
http://moldrefin.com/

Example for “scrolling” page concept as well as good balance of color, typography, and white space:
http://www.qorbitalmeet.eu/

Please contact us with questions so that we can guide your design effort.
Updates

Hello designers,

The following information is added to help guide the design process:

1.  For the text dialogue below the landing page, please assume the following word count:
"why are we making dad harbor?": 250 words
"who are we?" 200 words
"what's the deal with the penguin logo?" 300 words

For the social media links, please see http://www.gravelplumbs.com/
Notice the floating "social" bar that is always to the right.  This is the concept we are going for, please try to implement this as you see fit. 

Target Market(s)

Fathers of young children ages 0-6 years old.

Industry/Entity Type

Product

Font styles to use
Sans Serif

Requirements
Must have
• Clean lines, minimal design concept

Incorporation of our logo (see attached document)

Header content is static for all views after landing page, see example

This page WILL be responsive, please keep that in mind when designing
The timeline bar should be to the left, with the timeline bar’s “milestones” also being responsive.

Designer is free to suggest font types, but any fonts used must be royalty-free and web-optimized. We request a minimum number of font types as well as fonts that load relatively fast. We reinforce that visually appealing typography is a significant factor in the winning design choice.

While we are not expecting the winning design to include code, please keep in mind that the final implementation needs to be optimized for desktop, tablet, and mobile platforms.

If you are using stock photography that is not generated by you, please provide where/how we can obtain imagery, as well as price.

All custom graphics must be available in original formats; Photoshop/GIMP layered files for layout design, and vector formats for logos, icons and other graphical elements.

Please incorporate “Blue” into design elements as you see fit, as the RGB 67 74 169 Blue is the primary color used in our brand. The complement to this blue is 255 202 0, a brownish orange. Feel free to use this color as well, although please keep it to a lesser amount.

Background color is your choice, do not feel the need to use the grey.
Should not have
• Excessive graphical content such that it affects loading times

Excessive use of too many font types such that it affects loading times

```html
<!DOCTYPE html>
<html lang="en">
<head>
<meta charset="utf-8">
<title>DadHarbor – Prepare for the baby arrival</title>
<link href="https://fonts.googleapis.com/css2?family=Arvo&family=PT+Sans:wght@400;700&display=swap" rel="stylesheet">
<style>
:root{
  --brand-blue:#434aa9;
  --link-blue:#3b3f9a;
  --gold:#ffca00;
  --gold-text:#d9a21a;
  --ink:#444;
  --muted:#777;
  --line:#d9d9d9;
  --page:#f7f7f7;
  --white:#fff;
  --footer:#eeeeee;
  --green:#2e9a44;
}
*{box-sizing:border-box;margin:0;padding:0}
html,body{width:812px;height:1200px;overflow:hidden}
body{position:relative;background:var(--page);font-family:"PT Sans",Arial,sans-serif;color:var(--ink);font-size:11px}
.abs{position:absolute}
.site-header{position:absolute;left:0;top:0;width:812px;height:127px;background:var(--white);border-bottom:1px solid var(--line)}
.brand{position:absolute;left:68px;top:30px;width:120px;text-align:center}
.brand-dot{width:46px;height:46px;border-radius:50%;background:var(--brand-blue);margin:0 auto 8px}
.brand-name{font-weight:700;font-size:19px;color:var(--brand-blue)}
.welcome{position:absolute;right:68px;top:12px;font-family:"Arvo",Georgia,serif;font-size:18px;color:var(--gold-text)}
.search-input{position:absolute;left:476px;top:52px;width:206px;height:24px;border:1px solid #ccc;background:var(--white);padding:4px 10px;color:#999;font-size:10px;line-height:14px}
.search-btn{position:absolute;left:688px;top:52px;width:51px;height:24px;background:var(--gold);border:1px solid #e3a900;color:#8a5a00;font-size:10px;font-weight:700;text-align:center;line-height:22px}
.dad-score{position:absolute;left:476px;top:94px;color:var(--link-blue);font-size:11.5px;display:flex;align-items:center;gap:6px}
.account-links{position:absolute;right:73px;top:94px;color:var(--muted);font-size:11px}
.account-links span{margin:0 6px;color:#aaa}
.page-title{position:absolute;left:68px;top:147px;font-family:"Arvo",Georgia,serif;font-size:20px;color:#555}
.sort-label{position:absolute;left:614px;top:153px;color:var(--muted);font-size:9px}
.sort-select{position:absolute;left:651px;top:149px;width:93px;height:20px;border:1px solid #ccc;background:var(--white);font-size:9px;padding:3px 7px;color:#333}
.sort-select::after{content:"";position:absolute;right:7px;top:8px;border:3px solid transparent;border-top:4px solid #555}
.title-rule{position:absolute;left:68px;top:192px;width:676px;border-top:1px solid var(--line)}
.sidebar{position:absolute;left:68px;top:192px;width:165px;height:825px;background:var(--white);border:1px solid var(--line)}
.task-list{list-style:none;margin:0 6px}
.task{height:29.6px;border-bottom:1px solid #e6e6e6;display:flex;align-items:center;font-size:10.5px;color:#444;padding-left:12px}
.task:first-child{margin-top:0}
.task .box{width:8px;height:8px;border:1px solid #aaa;margin-right:9px;position:relative}
.task.done .box::after{content:"";position:absolute;left:1px;top:0;width:3px;height:5px;border:solid #555;border-width:0 1px 1px 0;transform:rotate(45deg)}
.promo{position:absolute;left:40px;top:267px;width:84px;height:424px;background:linear-gradient(#3a3d44,#4c5058 40%,#3d3f45 70%,#d07a22)}
.promo-photo{position:absolute;inset:0}
.promo-text{position:absolute;left:0;top:125px;width:84px;text-align:center;font-family:"Arvo",Georgia,serif;color:#fff;font-size:14px;line-height:21px}
.promo-btn{position:absolute;left:14px;top:217px;width:56px;height:15px;background:var(--green);border-radius:2px;color:#fff;font-size:8px;text-align:center;line-height:15px}
.card{position:absolute;width:228px;height:254px;background:var(--white);border:1px solid var(--line)}
.card-photo{position:absolute;left:4px;top:4px;width:218px;height:123px}
.badge{position:absolute;right:4px;top:95px;width:28px;height:30px;background:var(--gold);display:flex;align-items:center;justify-content:center}
.card-title{position:absolute;left:11px;top:136px;width:210px;font-family:"Arvo",Georgia,serif;font-size:11px;line-height:15.5px;color:var(--link-blue)}
.rating{position:absolute;left:11px;top:174px;display:flex;align-items:center;gap:8px;color:var(--muted);font-size:9.5px}
.card-text{position:absolute;left:11px;top:198px;width:210px;font-size:9px;line-height:15.5px;color:#666}
.reminder{position:absolute;left:0;top:1043px;width:812px;height:76px;background:var(--white);border-top:1px solid var(--line);border-bottom:1px solid var(--line);text-align:center;font-family:"Arvo",Georgia,serif;font-size:14.5px;line-height:24px;color:#333;padding-top:10px}
.site-footer{position:absolute;left:0;top:1119px;width:812px;height:81px;background:var(--footer)}
.footer-nav{position:absolute;left:68px;top:22px;font-size:9.5px;color:#555}
.footer-nav span{margin:0 6px;color:#aaa}
.copyright{position:absolute;left:68px;top:46px;font-size:9.5px;color:#555}
.social{position:absolute;left:663px;top:30px;display:flex;gap:9px}
.social i{display:block;width:21px;height:21px;border-radius:50%}
</style>
</head>
<body>

<header class="site-header">
  <div class="brand"><div class="brand-dot"></div><div class="brand-name">DadHarbor</div></div>
  <div class="welcome">Welcome Tomas, what would you like to do today?</div>
  <div class="search-input">Keyword...</div>
  <div class="search-btn">SEARCH</div>
  <div class="dad-score">
    <svg width="10" height="9" viewBox="0 0 10 9"><path d="M5 9 0.8 4.8A2.4 2.4 0 0 1 5 1.6 2.4 2.4 0 0 1 9.2 4.8Z" fill="var(--link-blue)"/></svg>
    Super Dad Score: 10,500
  </div>
  <div class="account-links">My Account<span>|</span>Log out</div>
</header>

<h1 class="page-title">Prepare for the baby arrival</h1>
<div class="sort-label">Sort by :</div>
<div class="sort-select">Most recent</div>
<div class="title-rule"></div>

<aside class="sidebar">
  <ul class="task-list">
    <li class="task"><i class="box"></i>Buy a crib</li>
    <li class="task"><i class="box"></i>Assemble the crib</li>
    <li class="task"><i class="box"></i>Buy a stroller</li>
    <li class="task done"><i class="box"></i>Buy a carseat</li>
    <li class="task"><i class="box"></i>Install a carseat</li>
    <li class="task"><i class="box"></i>Learn to change a diaper</li>
    <li class="task"><i class="box"></i>Learn to hold a baby</li>
    <li class="task"><i class="box"></i>Set a fedding schedule</li>
  </ul>
  <div class="promo">
    <div class="promo-photo" role="img" aria-label="Advertisement photo of a toddler in a car booster seat above a car seat product shot"></div>
    <div class="promo-text">Curabitur accumsan turpis fames</div>
    <div class="promo-btn">Read More</div>
  </div>
</aside>

<svg width="0" height="0" style="position:absolute">
  <defs>
    <symbol id="star" viewBox="0 0 12 12"><path d="M6 .5l1.6 3.6 3.9.4-2.9 2.6.8 3.9L6 9 2.6 11l.8-3.9L.5 4.5l3.9-.4Z" fill="#f5b800"/></symbol>
    <symbol id="half" viewBox="0 0 12 12"><path d="M6 .5l1.6 3.6 3.9.4-2.9 2.6.8 3.9L6 9 2.6 11l.8-3.9L.5 4.5l3.9-.4Z" fill="none" stroke="#f5b800"/><path d="M6 .5V9L2.6 11l.8-3.9L.5 4.5l3.9-.4Z" fill="#f5b800"/></symbol>
    <symbol id="doc" viewBox="0 0 16 18"><path d="M2 1h9l3 3v13H2Z" fill="#111"/><path d="M11 1v3h3" fill="none" stroke="var(--gold)"/></symbol>
    <symbol id="cart" viewBox="0 0 20 18"><path d="M1 2h3l2.5 9h10l2-7H5.5" fill="none" stroke="#111" stroke-width="1.8"/><path d="M7 5h11M7.5 8h9.5" stroke="#111"/><circle cx="8" cy="15" r="1.6" fill="#111"/><circle cx="15" cy="15" r="1.6" fill="#111"/></symbol>
    <symbol id="stars" viewBox="0 0 72 12"><use href="#star" x="0" width="12" height="12"/><use href="#star" x="15" width="12" height="12"/><use href="#star" x="30" width="12" height="12"/><use href="#star" x="45" width="12" height="12"/><use href="#half" x="60" width="12" height="12"/></symbol>
  </defs>
</svg>

<article class="card" style="left:259px;top:212px">
  <div class="card-photo" role="img" aria-label="Photo of a baby in a rear-facing car seat playing with a toy" style="background:linear-gradient(120deg,#9aa0a8,#3c4048 60%,#c9c9c9)"></div>
  <div class="badge"><svg width="14" height="16"><use href="#doc"/></svg></div>
  <h2 class="card-title">Pellentesque habitant morbi tristique senectus et netus</h2>
  <div class="rating"><svg width="72" height="12"><use href="#stars"/></svg>3,121 ratings</div>
  <p class="card-text">I went out to buy my first car seat and had to earn my PhD in car seats, Newtonian physics, and anti-stain technology…</p>
</article>

<article class="card" style="left:507px;top:212px">
  <div class="card-photo" role="img" aria-label="Photo of a smiling baby in an infant carrier seat" style="background:linear-gradient(120deg,#b9ad99,#4a3e35 55%,#d8d2c6)"></div>
  <div class="badge"><svg width="18" height="16"><use href="#cart"/></svg></div>
  <h2 class="card-title">Pellentesque habitant morbi tristique senectus et netus</h2>
  <div class="rating"><svg width="72" height="12"><use href="#stars"/></svg>3,121 ratings</div>
  <p class="card-text">I went out to buy my first car seat and had to earn my PhD in car seats, Newtonian physics, and anti-stain technology…</p>
</article>

<article class="card" style="left:259px;top:487px">
  <div class="card-photo" role="img" aria-label="Photo of a laughing toddler in a car seat inside a red car" style="background:linear-gradient(120deg,#a8432a,#7a4a30 45%,#c8a27c)"></div>
  <div class="badge"><svg width="14" height="16"><use href="#doc"/></svg></div>
  <h2 class="card-title">Pellentesque habitant morbi tristique senectus et netus</h2>
  <div class="rating"><svg width="72" height="12"><use href="#stars"/></svg>3,121 ratings</div>
  <p class="card-text">I went out to buy my first car seat and had to earn my PhD in car seats, Newtonian physics, and anti-stain technology…</p>
</article>

<article class="card" style="left:507px;top:487px">
  <div class="card-photo" role="img" aria-label="Photo of a baby buckled into a grey and orange infant seat" style="background:linear-gradient(90deg,#3b3d42,#55575c 50%,#3b3d42)"></div>
  <div class="badge"><svg width="18" height="16"><use href="#cart"/></svg></div>
  <h2 class="card-title">Pellentesque habitant morbi tristique senectus et netus</h2>
  <div class="rating"><svg width="72" height="12"><use href="#stars"/></svg>3,121 ratings</div>
  <p class="card-text">I went out to buy my first car seat and had to earn my PhD in car seats, Newtonian physics, and anti-stain technology…</p>
</article>

<article class="card" style="left:259px;top:763px">
  <div class="card-photo" role="img" aria-label="Photo of a baby under a car seat belt" style="background:linear-gradient(120deg,#5f6a70,#8a9296 50%,#6b7176)"></div>
  <div class="badge"><svg width="14" height="16"><use href="#doc"/></svg></div>
  <h2 class="card-title">Pellentesque habitant morbi tristique senectus et netus</h2>
  <div class="rating"><svg width="72" height="12"><use href="#stars"/></svg>3,121 ratings</div>
  <p class="card-text">I went out to buy my first car seat and had to earn my PhD in car seats, Newtonian physics, and anti-stain technology…</p>
</article>

<article class="card" style="left:507px;top:763px">
  <div class="card-photo" role="img" aria-label="Photo of a sleeping baby in a dark car seat" style="background:linear-gradient(120deg,#3a2c24,#8a6e5c 50%,#c8d2e0)"></div>
  <div class="badge"><svg width="18" height="16"><use href="#cart"/></svg></div>
  <h2 class="card-title">Pellentesque habitant morbi tristique senectus et netus</h2>
  <div class="rating"><svg width="72" height="12"><use href="#stars"/></svg>3,121 ratings</div>
  <p class="card-text">I went out to buy my first car seat and had to earn my PhD in car seats, Newtonian physics, and anti-stain technology…</p>
</article>

<section class="reminder">
  Your big day is almost here! Do you have your go-back packed?<br>
  Do you have your routes (plural!) to the hospital mapped out? Lots to do, not much time!
</section>

<footer class="site-footer">
  <nav class="footer-nav">Home<span>/</span>About us<span>/</span>Products<span>/</span>Articles<span>/</span>Contact us</nav>
  <div class="copyright">Copyright &nbsp;©&nbsp; 2013 &nbsp; DadHarbor. &nbsp; All rights reserved.</div>
  <div class="social">
    <i style="background:#3b5998"></i>
    <i style="background:#36a9e1"></i>
    <svg width="21" height="21" viewBox="0 0 21 21"><circle cx="10.5" cy="10.5" r="10.5" fill="#666"/><path d="M6 12.5l4.5-4.5 4.5 4.5" fill="none" stroke="#fff" stroke-width="2.2"/></svg>
  </div>
</footer>

</body>
</html>
```